Design and Renovation Company Luxury Business Card

I want to create a luxury business card for a Design and Renovation Firm . We will use our current logo. The company name is 528BUILDA. We do not want anything standard. We need a very unique concept.
Please see uploaded inspiration. I really like the textured paper option. I would like the card to be thick with debossing, and/or embossing options. The logo has orange in it but I would like to see the card with and without the orange. I think the orange may make the company feel less high-end. The goal is to elevate the logo not match its vibe per se of the logo. We want something very unique, not standard at all!
I would like a space for :
Logo,
Name,
Position,
Email,
Office number,
Website Address,
Business Address,
Thank you!
Have fun!
Target Market(s)
Home owners Age 35 +
Industry/Entity Type
Design and Renovation
Contact Information for Business Card
Logo, Name, Position, Email, Office number, Website Address, Business Address,.
Colors
Designer to choose colors to be used in the design.
Requirements
Must have
- A luxury designer feel. Must be black or dark grey but open to other luxury ideas.
Nice to have
- Gold, silver, black embossing or debossing. Textured paper design.
Should not have
- A cheap look and feel.

```html
<!DOCTYPE html>
<html lang="en">
<head>
<meta charset="utf-8">
<title>528BUILDA Business Card</title>
<link href="https://fonts.googleapis.com/css2?family=Montserrat:wght@400;500;600;700&display=swap" rel="stylesheet">
<style>
  :root {
    --backdrop: #9b9b9b;
    --paper-white: #f6f6f4;
    --paper-black: #1d1d1d;
    --ink-dark: #222222;
    --ink-light: #f2f2f2;
    --accent-orange: #e8911e;
    --edge-orange: #d77a10;
    --faint-grey: #e0e0e0;
  }
  * { margin: 0; padding: 0; box-sizing: border-box; }
  html, body {
    width: 1200px; height: 956px; overflow: hidden;
    background: var(--backdrop);
    font-family: "Montserrat", Arial, sans-serif;
  }
  .stage { position: relative; width: 1200px; height: 956px; }

  .card {
    position: absolute;
    width: 620px; height: 354px;
    border-bottom: 4px solid var(--edge-orange);
    box-shadow: 0 18px 40px rgba(0,0,0,0.28);
  }
  .card-front { left: 150px; top: 90px; background: var(--paper-white); z-index: 2; }
  .card-back  { left: 430px; top: 500px; background: var(--paper-black); z-index: 1; }

  .brand { display: flex; align-items: center; gap: 10px; }
  .brand-square { width: 26px; height: 26px; background: var(--accent-orange); }
  .brand-name { font-weight: 600; letter-spacing: 3px; }

  .card-front .brand { position: absolute; left: 42px; top: 40px; }
  .card-front .brand-name { font-size: 34px; color: var(--ink-dark); }
  .card-front .tagline {
    position: absolute; left: 78px; top: 86px;
    font-size: 10px; letter-spacing: 3.5px; color: var(--ink-dark);
  }

  .person { position: absolute; left: 42px; top: 128px; color: var(--ink-dark); }
  .person-name { font-size: 22px; font-weight: 700; color: var(--accent-orange); letter-spacing: 1px; }
  .person-role { font-size: 13px; margin-top: 2px; }
  .address { font-size: 13px; line-height: 1.45; margin-top: 12px; }

  .contact-list { list-style: none; margin-top: 12px; font-size: 13px; }
  .contact-list li { display: flex; align-items: center; gap: 9px; line-height: 1.75; }
  .contact-list svg { width: 12px; height: 12px; flex: none; }

  .faint-block {
    position: absolute; right: 56px; bottom: 50px;
    width: 150px; height: 150px; background: var(--faint-grey);
  }

  .card-back .brand-wrap {
    position: absolute; left: 0; right: 0; top: 118px;
    display: flex; flex-direction: column; align-items: center;
  }
  .card-back .brand-square { width: 40px; height: 40px; }
  .card-back .brand-name { font-size: 56px; color: var(--ink-light); letter-spacing: 5px; }
  .card-back .tagline {
    margin-top: 8px; font-size: 15px; font-weight: 500;
    letter-spacing: 6px; color: var(--ink-light);
  }
</style>
</head>
<body>
<main class="stage">

  <section class="card card-front" aria-label="Business card front">
    <div class="brand">
      <span class="brand-square"></span>
      <span class="brand-name">528BUILDA</span>
    </div>
    <p class="tagline">Design and Renovation Firm</p>

    <div class="person">
      <p class="person-name">DAREL QUINN</p>
      <p class="person-role">Medical Director</p>
      <p class="address">418 Alder Crest Avenue Suite<br>312 Brookhaven, New York 11719</p>
      <ul class="contact-list">
        <li>
          <svg viewBox="0 0 12 12" aria-hidden="true"><path d="M3 1l2 2.5-1.2 1.3a6 6 0 0 0 3.4 3.4L8.5 7 11 9l-1 2C5 11 1 7 1 2z" fill="var(--accent-orange)"/></svg>
          (000)524-3918
        </li>
        <li>
          <svg viewBox="0 0 12 12" aria-hidden="true"><rect x="0.5" y="2" width="11" height="8" fill="var(--accent-orange)"/><path d="M1 2.5l5 4 5-4" stroke="#fff" fill="none"/></svg>
          hello@528builda.com
        </li>
        <li>
          <svg viewBox="0 0 12 12" aria-hidden="true"><circle cx="6" cy="6" r="5.5" fill="var(--accent-orange)"/><path d="M1 6h10M6 .5c-2.5 3-2.5 8 0 11M6 .5c2.5 3 2.5 8 0 11" stroke="#fff" stroke-width="0.7" fill="none"/></svg>
          www.528builda.com
        </li>
      </ul>
    </div>

    <div class="faint-block"></div>
  </section>

  <section class="card card-back" aria-label="Business card back">
    <div class="brand-wrap">
      <div class="brand">
        <span class="brand-square"></span>
        <span class="brand-name">528BUILDA</span>
      </div>
      <p class="tagline">Design and Renovation Firm</p>
    </div>
  </section>

</main>
</body>
</html>
```